Modern Business Card

Modern professional business card with more than just logo and demographic info. Something memorable.

We are a trendy/modern chiropractic group with an emphasis on neurology, hence the minimalist-type brain logo. We want to convey that modern and technical aspect with professionalism and the elite nature of our practice environment.

```html
<!DOCTYPE html>
<html lang="en">
<head>
<meta charset="utf-8">
<title>Meridian Spine – Business Card</title>
<link href="https://fonts.googleapis.com/css2?family=Open+Sans:wght@400;700&display=swap" rel="stylesheet">
<style>
  :root {
    --backdrop: #3a322d;
    --card: #262728;
    --card-back: #1f2021;
    --ink: #f2f2f2;
    --accent: #3f7fd0;
    --deboss: #2b2c2e;
  }
  * { margin: 0; padding: 0; box-sizing: border-box; }
  html, body { width: 1200px; height: 847px; overflow: hidden; }
  body {
    background: var(--backdrop);
    font-family: "Open Sans", Arial, sans-serif;
    position: relative;
  }
  .card {
    position: absolute;
    width: 540px;
    height: 308px;
    border-radius: 3px;
    box-shadow: 0 14px 30px rgba(0,0,0,.45);
  }
  /* back side */
  .card-back {
    left: 60px; top: 110px;
    background: var(--card-back);
    display: flex; align-items: center; justify-content: center; gap: 18px;
  }
  .card-back .mark-square {
    width: 40px; height: 40px; background: var(--deboss);
  }
  .card-back .brand-name {
    font-weight: 700; font-size: 46px; line-height: 1.05; letter-spacing: 3px;
    color: var(--deboss); text-transform: uppercase;
  }
  /* front side */
  .card-front {
    left: 600px; top: 440px;
    background: var(--card);
    color: var(--ink);
  }
  .brand {
    position: absolute; left: 36px; top: 116px;
    display: flex; align-items: center; gap: 12px;
  }
  .brand .mark-square { width: 26px; height: 26px; background: var(--accent); flex: none; }
  .brand .brand-name {
    font-weight: 700; font-size: 26px; line-height: 1.05; letter-spacing: 1.5px;
    color: var(--ink); text-transform: uppercase;
  }
  .divider {
    position: absolute; left: 268px; top: 86px;
    width: 2px; height: 156px; background: var(--accent);
  }
  .details {
    position: absolute; left: 286px; top: 84px;
    font-size: 14px; line-height: 1.38;
    white-space: nowrap;
  }
  .person-name {
    font-weight: 700; font-size: 18px; color: var(--accent);
    text-transform: uppercase; letter-spacing: .5px;
  }
  .person-role { margin-bottom: 8px; }
  .address { margin-bottom: 8px; }
  .contact-list { list-style: none; }
  .contact-list li { display: flex; align-items: center; gap: 6px; }
  .contact-list svg { width: 11px; height: 11px; fill: var(--accent); flex: none; }
</style>
</head>
<body>
  <div class="card card-back">
    <span class="mark-square"></span>
    <span class="brand-name">Meridian<br>Spine</span>
  </div>

  <div class="card card-front">
    <div class="brand">
      <span class="mark-square"></span>
      <span class="brand-name">Meridian<br>Spine</span>
    </div>
    <div class="divider"></div>
    <div class="details">
      <div class="person-name">Daniel Rourke</div>
      <div class="person-role">President</div>
      <div class="address">1180 Harbor Crest Way<br>Seacliff CA 92700</div>
      <ul class="contact-list">
        <li>
          <svg viewBox="0 0 24 24" aria-hidden="true"><path d="M6.6 10.8a15.1 15.1 0 0 0 6.6 6.6l2.2-2.2c.3-.3.7-.4 1-.2 1.1.4 2.3.6 3.6.6.6 0 1 .4 1 1V20c0 .6-.4 1-1 1C10.6 21 3 13.4 3 4c0-.6.4-1 1-1h3.5c.6 0 1 .4 1 1 0 1.3.2 2.5.6 3.6.1.3 0 .7-.2 1z"/></svg>
          555-240-0187
        </li>
        <li>
          <svg viewBox="0 0 24 24" aria-hidden="true"><path d="M2 5h20v14H2z M2 5l10 8 10-8" fill="none" stroke="#3f7fd0" stroke-width="2"/><path d="M3 6l9 7 9-7v12H3z"/></svg>
          daniel@meridianspine.com
        </li>
        <li>
          <svg viewBox="0 0 24 24" aria-hidden="true"><circle cx="12" cy="12" r="10"/><path d="M2 12h20M12 2c3 3 3 17 0 20M12 2c-3 3-3 17 0 20" fill="none" stroke="#262728" stroke-width="1.5"/></svg>
          www.meridianspine.com
        </li>
      </ul>
    </div>
  </div>
</body>
</html>
```